Design a business card
Business name: Harbourline Growth Advisory
Improving Business Profitibility

- An Overview of the Business & Service:

Business Performance Consulting

- The Target Market: Small to medium-sized business

- Design Specifics:
White card, blue ink, moon eclipse

No Logo

Target Market(s)

Small to medium-sized business

Font styles to use
Sans Serif

```html
<!DOCTYPE html>
<html lang="en">
<head>
<meta charset="utf-8">
<title>Harbourline Growth Advisory – Business Card</title>
<link href="https://fonts.googleapis.com/css2?family=Open+Sans:wght@400;600&family=Oswald:wght@500&display=swap" rel="stylesheet">
<style>
  :root {
    --page-bg: #eceae6;
    --card-white: #ffffff;
    --card-black: #050505;
    --brand-blue: #0d4a8f;
    --brand-green: #5cc21c;
    --text-dark: #3a3a3a;
    --rule-grey: #555555;
    --photo-red: #7a1e14;
  }
  * { box-sizing: border-box; margin: 0; padding: 0; }
  html, body {
    width: 1200px; height: 900px; overflow: hidden;
    background: var(--page-bg);
    font-family: "Open Sans", Arial, sans-serif;
  }
  .canvas { position: relative; width: 1200px; height: 900px; }
  .card {
    position: absolute; left: 320px; width: 560px; height: 320px;
    overflow: hidden;
    box-shadow: 0 6px 18px rgba(0,0,0,0.18);
  }
  /* Back side */
  .card-back { top: 100px; background: var(--card-black); }
  .eclipse-photo {
    position: absolute; left: 210px; top: 44px; width: 140px; height: 116px;
    background: radial-gradient(ellipse at 50% 50%, var(--photo-red) 0%, #2a0805 55%, var(--card-black) 100%);
  }
  .back-rule {
    position: absolute; left: 130px; right: 130px; top: 190px;
    height: 1px; background: var(--rule-grey);
  }
  .tagline {
    position: absolute; left: 0; right: 0; top: 222px;
    text-align: center; color: #f2f2f2;
    font-size: 13.5px; letter-spacing: 0.6px; text-transform: uppercase;
  }
  /* Front side */
  .card-front { top: 480px; background: var(--card-white); }
  .person { position: absolute; left: 48px; top: 40px; }
  .person-name {
    font-family: "Oswald", "Arial Narrow", sans-serif; font-weight: 500;
    font-size: 22px; letter-spacing: 0.3px; text-transform: uppercase; line-height: 1.1;
  }
  .person-name .first { color: var(--brand-blue); }
  .person-name .last { color: var(--brand-green); }
  .person-role { color: var(--text-dark); font-size: 15px; margin-top: 2px; }
  .company-name {
    position: absolute; right: 36px; top: 42px; width: 240px;
    color: var(--brand-blue); font-weight: 600; font-size: 22px;
    line-height: 1.15;
  }
  .contact { position: absolute; left: 48px; top: 124px; color: var(--text-dark); }
  .contact-line { display: flex; align-items: center; gap: 8px; font-size: 15px; line-height: 21px; }
  .contact-line svg { width: 13px; height: 13px; flex: none; }
  .address { margin-top: 10px; font-size: 15.5px; line-height: 21px; }
  .wave { position: absolute; left: 0; top: 0; width: 560px; height: 320px; }
  .website {
    position: absolute; right: 28px; top: 222px;
    color: #ffffff; font-size: 13.5px;
  }
</style>
</head>
<body>
<main class="canvas">
  <section class="card card-back" aria-label="Card back">
    <div class="eclipse-photo" role="img" aria-label="Photograph of a red lunar eclipse"></div>
    <div class="back-rule"></div>
    <p class="tagline">Improving Business Profitibility</p>
  </section>

  <section class="card card-front" aria-label="Card front">
    <svg class="wave" viewBox="0 0 560 320" aria-hidden="true">
      <path d="M0 304 C150 300 250 245 360 190 C440 158 510 150 560 148 L560 320 L0 320 Z" fill="var(--brand-blue)"/>
      <path d="M0 282 C130 284 240 240 345 192 C250 248 140 292 0 297 Z" fill="var(--brand-green)"/>
    </svg>

    <div class="person">
      <p class="person-name"><span class="first">Rowan</span> <span class="last">Ellery</span></p>
      <p class="person-role">Managing Director</p>
    </div>

    <p class="company-name">Harbourline Growth Advisory</p>

    <div class="contact">
      <p class="contact-line">
        <svg viewBox="0 0 16 16"><path d="M2 6 C2 3 14 3 14 6 L11 7 L10 5.5 L6 5.5 L5 7 Z M4 8 L12 8 L13 13 L3 13 Z" fill="var(--brand-blue)"/></svg>
        021-555 014 372
      </p>
      <p class="contact-line">
        <svg viewBox="0 0 16 16"><rect x="4" y="1" width="8" height="14" rx="1.5" fill="none" stroke="var(--brand-blue)" stroke-width="1.6"/><rect x="7" y="12" width="2" height="1.4" fill="var(--brand-blue)"/></svg>
        021-555 014 372
      </p>
      <p class="contact-line">
        <svg viewBox="0 0 16 16"><rect x="1" y="3" width="14" height="10" fill="var(--brand-blue)"/><path d="M1 3 L8 9 L15 3" fill="none" stroke="#ffffff" stroke-width="1.3"/></svg>
        hello@harbourlinegrowth.com
      </p>
      <p class="address">48 Quayside Row,<br>Marlow Bay, 40217.</p>
    </div>

    <p class="website">www.harbourlinegrowth.com</p>
  </section>
</main>
</body>
</html>
```